To design a brand identity that is simple and creative with 'Corvane' as the brand name, I like modern simple fonts like helvetica neue, I want to print both sides of the card, I am open to dark front and white back, but the design needs to transfer well to letter heads and email signatures, I am looking for sophisticated and elegant, but open minded about clever and off the wall, I do not do 'boring' Corvane Ventures is the mother company for a small group, specialising in Management & consulting, Software development and construction, we have a high level of integrity, we are transparent and accountable for what we do. my images are provided as a guide only, Im not expecting them to be just copied, Im looking for a creator and passionate thinker, who will put life into their work.

Target Market(s)

usually business minded people who are looking for something different in me, such as leadership, confidence and focus with thinking that is per haps a little outside the box..

Industry/Entity Type

Construction

Requirements
Must have
• clean, minmalistic
Nice to have
• custom logo
Should not have
• boring, traditional

```html
<!DOCTYPE html>
<html lang="en">
<head>
<meta charset="utf-8">
<title>Corvane Ventures – Business Card</title>
<link rel="stylesheet" href="https://fonts.googleapis.com/css2?family=Inter:wght@300;400&family=Dancing+Script:wght@500&display=swap">
<style>
  :root {
    --stage: #3a3633;
    --amber-light: #b07d2c;
    --amber-mid: #9a6a25;
    --amber-dark: #7e561e;
    --cream: #f3ead9;
    --cream-soft: #e6d6bb;
    --amber-ghost: rgba(214, 160, 80, 0.45);
    --charcoal-light: #57524f;
    --charcoal: #343232;
    --charcoal-dark: #262525;
    --white: #ffffff;
    --silver: #d9d6d3;
    --red: #d8232a;
    --label: #e8e5e2;
    --text-font: "Inter", "Helvetica Neue", Arial, sans-serif;
    --script-font: "Dancing Script", cursive;
  }
  * { margin: 0; padding: 0; box-sizing: border-box; }
  html, body { width: 1000px; height: 1200px; overflow: hidden; }
  body {
    position: relative;
    background: var(--stage);
    font-family: var(--text-font);
  }
  .side-label {
    position: absolute;
    color: var(--label);
    font-size: 20px;
    font-weight: 400;
  }
  .side-label--front { left: 811px; top: 569px; }
  .side-label--back { left: 117px; top: 1143px; }

  .card {
    position: absolute;
    width: 740px;
    height: 458px;
    overflow: hidden;
  }

  /* Front */
  .card--front { left: 136px; top: 74px; }
  .card__texture {
    position: absolute; inset: 0;
    background: linear-gradient(135deg, var(--amber-light) 0%, var(--amber-mid) 50%, var(--amber-dark) 100%);
  }
  .brand-mark {
    position: absolute;
    border-radius: 50%;
    background: var(--cream);
  }
  .card--front .brand-mark { left: 46px; top: 213px; width: 44px; height: 44px; }
  .brand-name {
    position: absolute;
    font-weight: 300;
    line-height: 1;
  }
  .card--front .brand-name { left: 134px; top: 206px; font-size: 50px; color: var(--white); }
  .brand-tagline {
    position: absolute;
    left: 138px; top: 262px;
    width: 156px;
    text-align: right;
    font-family: var(--script-font);
    font-size: 16px;
    color: var(--white);
  }
  .ghost-word {
    position: absolute;
    left: 370px; top: 230px;
    transform: translate(-50%, -50%) rotate(-90deg);
    font-size: 92px;
    font-weight: 300;
    color: var(--amber-ghost);
    white-space: nowrap;
  }
  .divisions-vertical {
    position: absolute;
    left: 370px; top: 230px;
    transform: translate(-50%, -50%) rotate(-90deg);
    font-size: 15px;
    letter-spacing: 1.2px;
    color: var(--white);
    white-space: nowrap;
  }
  .contact {
    position: absolute;
    left: 454px; top: 136px;
    color: var(--cream-soft);
  }
  .contact__name { font-size: 26px; font-weight: 400; color: var(--white); line-height: 1.2; }
  .contact__role { font-size: 15px; color: var(--white); margin-bottom: 10px; }
  .contact__line { font-size: 18px; font-weight: 300; line-height: 28px; letter-spacing: 0.4px; }
  .contact__line--gap { margin-top: 14px; }

  /* Back */
  .card--back {
    left: 117px; top: 652px;
    background: radial-gradient(ellipse at 50% 35%, var(--charcoal-light) 0%, var(--charcoal) 55%, var(--charcoal-dark) 100%);
  }
  .card--back .brand-mark { left: 140px; top: 180px; width: 88px; height: 88px; background: var(--white); }
  .card--back .brand-name { left: 258px; top: 168px; font-size: 96px; color: var(--white); }
  .divisions {
    position: absolute;
    left: 0; right: 0; top: 296px;
    text-align: center;
    font-size: 16px;
    letter-spacing: 1.5px;
    color: var(--silver);
  }
  .divisions__dot { color: var(--red); margin: 0 6px; font-size: 12px; vertical-align: 1px; }
</style>
</head>
<body>
  <section class="card card--front" aria-label="Card front">
    <div class="card__texture" role="img" aria-label="Faceted amber low-poly background pattern"></div>
    <span class="brand-mark" aria-hidden="true"></span>
    <span class="brand-name">corvane</span>
    <span class="brand-tagline">... in the creation business</span>
    <span class="ghost-word" aria-hidden="true">corvane</span>
    <span class="divisions-vertical">management • software • construction</span>
    <div class="contact">
      <p class="contact__name">Mara Lindqvist</p>
      <p class="contact__role">client ambassador</p>
      <p class="contact__line">c. +61 0400 555 217</p>
      <p class="contact__line">e. info@corvane.com.au</p>
      <p class="contact__line contact__line--gap">a. po box 418 perth 6000</p>
      <p class="contact__line">w. www.corvane.ventures</p>
    </div>
  </section>
  <p class="side-label side-label--front">Front</p>

  <section class="card card--back" aria-label="Card back">
    <span class="brand-mark" aria-hidden="true"></span>
    <span class="brand-name">corvane</span>
    <p class="divisions">management<span class="divisions__dot">●</span>software<span class="divisions__dot">●</span>construction</p>
  </section>
  <p class="side-label side-label--back">Back</p>
</body>
</html>
```